LADIES' HARBOR COLLECTIVE

Design a website for a membership based organization focusing on entrepreneurship, women's issues and global news regarding commerce.
Also, want a news daily tie in to site, and social media outlets.
I want the colors in strong blue, deep or metallic gold and cream/white like logo which will be provided. I want logo altered with globe to replace small sphere in the design.
Also, board members page that should be redesigned. Might need extra coding.
PLEASE SEE http://ladiesharborcollective.example DIDN'T LIKE THIS LAY OUT AT ALL TOO MUCH WHITE AND NOT ENOUGH IMPACT. WANT TO DRAW MEMBERS.

PLEASE SEE http://www.qrtv-sample.example/Index.cfm BUT THIS IS WAY TO BUSY BUT I LIKE THE SLIDING.

SEE OUR TWITTER ACCOUNT FOR INSIGHT. @LADIESHARBCOL

Reason: Happy Holidays. The board approving the design will be out on season time vacation until Jan. 2. Please make any edits requested from designer already submitting layouts. Thank you, Odette

Target Market(s)

GLOBAL BUSINESS WOMEN AND ENTREPRENEURS AGES 20-65

Industry/Entity Type

Media

Number of Pages Required

4 page

Font styles to use
Other font styles liked:
• Baskerville or something similar

Colors
fbed22
3377b5
9bcb3c

Requirements
Must have
• Show diversity of ethnicities if using stock photos. Vibrant and inviting site, MUST JOIN or Be part of this organization. Luxury style
• THIS IS A FOR PROFIT WEBSITE.
• Membership Fees:
• Annual Fee $250
• For an additional fee of $150 you can grow your visibility and voice through our Ladies' Harbor Collective Bulletin and Speaker's Bureau (LHCBSB).
• LHC Speaker's Bureau will support your personal, business and organizations' objectives and to give you greater visibility and voice as an authority world leader or business visionary in your field of service.
• LHCSB realizes that so many worthy leaders' in diverse fields of service are never allowed to be heard. If you feel you are a dynamic speaker, run a worthwhile business or organization and whose wisdom and success can be of service of others sign up today and be part of the LHCSB!
• Student Membership
• Discounted student memberships are also available. Students have access to selected group forums, as well as selected groups of members that provide mentoring. Mentoring helps continue the member's legacy and creates a well spring of future leaders. Student membership fees cost just $75 a year.
• Contact us to help promote you and other women's vision throughout the world.
• Join LHC Now!
• CAN YOU PROVIDE A HEADLINE WITHOUT WOMEN SEE TWITTER ACCOUNT.
Nice to have
• Nice headline and well position tabs.
• Home
• Join LHC Now
• Memberships
• LHC Team Leadership
• About Us
• Contact
• LHC is an Effective Women's Initiative for You!
• New Member - Women's Organization
• 20% Discount- Offer Valid on Your Membership Fee When You Join before 1/30/2105
• Memberships
• LHC Leadership
• At Ladies' Harbor Collective, we offer the opportunity to connect with women throughout the globe. Join these trailblazers to shorten your path to success and camaraderie.
• Who We Are
• Ladies' Harbor Collective is an online women's initiative that promotes your business and visions through social engagement. We are here to help you form strategic partnerships with like-minded women around the world. End your solo journey by becoming a member of LHC.
• LHC also features a forum to promote the services, campaigns, and social activism by our members.
• LHC is about women helping other women. Contact us for more information.
• Learn More about Ladies' Harbor Collective
• Contact us for more information in regards to LHC membership and how to get involved.
• SHARE THIS PAGE:
• twitter, fb, instagram, etc.

```html
<!DOCTYPE html>
<html lang="en">
<head>
<meta charset="utf-8">
<title>Ladies' Harbor Collective</title>
<link rel="stylesheet" href="https://fonts.googleapis.com/css2?family=Open+Sans:ital,wght@0,400;0,600;1,400&family=Gochi+Hand&display=swap">
<style>
:root{
  --blue:#2a84b8;
  --blue-dark:#1f6f9f;
  --gold:#f3b21b;
  --ink:#333;
  --grey:#9a9a9a;
  --panel:#1c1c1c;
  --panel-2:#343434;
  --footer:#333333;
  --footer-line:#4a4a4a;
  --white:#fff;
}
*{box-sizing:border-box;margin:0;padding:0}
html,body{width:851px;height:1200px;overflow:hidden;background:var(--white)}
body{position:relative;font-family:'Open Sans',Arial,sans-serif;color:var(--ink)}
.abs{position:absolute}
h1,h2,h3{font-weight:400}

/* header */
.brand{left:70px;top:62px;display:flex;align-items:center;gap:6px}
.brand-mark{width:12px;height:12px;border-radius:50%;background:var(--gold)}
.brand-name{font-size:11px;color:#1e3f73;font-weight:600;letter-spacing:-.2px;white-space:nowrap}
.brand-tag{left:70px;top:80px;font-size:4.6px;color:#1e3f73;font-weight:600;text-transform:uppercase;white-space:nowrap}
.btn-pill{top:14px;height:19px;width:62px;border-radius:10px;background:#c9cccf;color:var(--white);font-size:7px;text-align:center;line-height:19px;text-transform:uppercase}
.social{top:15px;width:20px;height:20px;border-radius:50%;border:2px solid #d6d6d6}
.call-icon{left:527px;top:57px;width:20px;height:20px;border-radius:50%;background:#3a3a3a;border:2px solid #ccc}
.call{left:556px;top:67px;font-size:9px;font-style:italic;color:#444;white-space:nowrap}
.call b{font-weight:600;font-size:9.5px}
.search{left:682px;top:58px;width:99px;height:20px;border:1px solid #ddd;border-radius:3px;font-size:7px;font-style:italic;color:#aaa;padding:5px 9px}

/* nav */
.nav{left:70px;top:106px;width:711px;height:24px}
.nav a{position:absolute;top:0;height:24px;line-height:24px;font-size:8px;color:#444;text-decoration:none;text-transform:uppercase;transform:translateX(-50%);white-space:nowrap}
.nav a.active{left:0;transform:none;width:63px;background:var(--blue);color:var(--white);text-align:center;border-radius:5px 5px 0 0}
.nav-rule{left:0;top:129px;width:851px;height:3px;background:var(--blue)}

/* hero */
.hero{left:70px;top:133px;width:711px;height:295px;border:1px solid #ddd;background:linear-gradient(90deg,#f4f2ef 0%,#e7e3de 35%,#efece8 60%,#e9e6e2 100%)}
.hero-person{left:454px;top:10px;width:196px;height:285px;background:linear-gradient(180deg,#d9bf95 0%,#3a3c44 45%,#1f2128 100%);border-radius:90px 90px 0 0}
.hero-title{left:47px;top:98px;width:430px;font-family:'Gochi Hand',cursive;font-size:16.5px;color:#333;white-space:nowrap;text-align:center}
.hero-copy{left:47px;top:130px;width:430px;font-size:7.3px;line-height:14px;color:var(--blue);text-align:center;text-transform:uppercase}
.btn-gold{background:var(--gold);color:var(--white);font-size:7px;text-align:center;text-transform:uppercase;border-radius:2px}
.hero .btn-gold{left:205px;top:172px;width:75px;height:21px;line-height:21px}
.arrow{top:137px;width:22px;height:18px;background:#9d9d9d}

/* intro blocks */
.who{left:70px;top:452px;width:468px;height:169px;background:var(--panel)}
.who-photo{left:0;top:0;width:215px;height:169px;background:linear-gradient(90deg,#cfd2d4 0%,#8b7467 50%,#2a2626 100%)}
.who-body{left:215px;top:0;width:253px;height:169px;text-align:center;color:var(--white)}
.block-title{font-size:15px;font-weight:400;text-transform:uppercase;letter-spacing:.3px}
.block-text{font-size:7.4px;line-height:14px}
.member{left:558px;top:452px;width:223px;height:169px;background:var(--panel-2);text-align:center;color:var(--white)}

/* leadership */
.section-title{left:0;width:851px;text-align:center;font-size:14px;font-weight:400;color:#3a3a3a;text-transform:uppercase}
.section-title b{color:var(--blue);font-weight:600}
.card{top:708px;width:220px;height:94px;border:1px solid #ddd;text-align:center}
.card p{position:absolute;left:0;top:38px;width:100%;font-size:7.4px;line-height:14px;color:#444}
.card a{position:absolute;left:0;top:73px;width:100%;font-size:8px;color:var(--gold);text-decoration:none}
.avatar{left:80px;top:-28px;width:56px;height:56px;border-radius:50%;border:2px solid #eee;background:radial-gradient(circle at 50% 40%,#d8b79a 0%,#8a6a55 60%,#4a3b33 100%)}

/* contact band */
.band{left:70px;top:861px;width:711px;height:105px;background:var(--blue)}
.user-disc{left:24px;top:26px;width:52px;height:52px;border-radius:50%;background:var(--white)}
.field{top:41px;width:145px;height:23px;background:var(--white);font-size:7px;color:#aaa;line-height:23px;padding-left:9px;text-transform:uppercase}
.band .btn-gold{left:573px;top:41px;width:107px;height:23px;line-height:23px}

/* footer */
.footer{left:0;top:966px;width:851px;height:234px;background:var(--footer);color:#ddd}
.foot-h{top:25px;font-size:9.5px;font-weight:600;color:var(--white);text-transform:uppercase}
.foot-h::after{content:"";display:block;width:100px;height:1px;background:#777;margin-top:5px}
.foot-p{left:70px;width:210px;font-size:7.4px;line-height:14px;text-align:justify}
.foot-list{list-style:none;font-size:7.4px;line-height:18.2px;white-space:nowrap}
.foot-list li::before{content:"›";margin-right:5px}
.thumb{width:53px;height:43px;background:linear-gradient(135deg,#d9dde2,#6f7b88)}
.foot-rule{left:0;top:178px;width:851px;height:1px;background:var(--footer-line)}
.foot-links{left:70px;top:191px;font-size:7px;color:var(--white);text-transform:uppercase;white-space:nowrap}
.copy{right:70px;top:191px;font-size:7px;color:var(--white);white-space:nowrap}
</style>
</head>
<body>

<header>
  <div class="abs brand"><span class="brand-mark"></span><span class="brand-name">Ladies' Harbor Collective</span></div>
  <div class="abs brand-tag">Women connecting across every harbor</div>

  <div class="abs btn-pill" style="left:526px">Signup</div>
  <div class="abs btn-pill" style="left:599px">Login</div>

  <span class="abs social" style="left:687px;background:#3b5a98"></span>
  <span class="abs social" style="left:711px;background:#d34836"></span>
  <span class="abs social" style="left:735px;background:#2fa8df"></span>
  <span class="abs social" style="left:759px;background:#c8232c"></span>

  <div class="abs call-icon">
    <svg width="16" height="16" viewBox="0 0 16 16"><path d="M5 4c1 0 1.5 2 1 2.6l-.6.6c.5 1.2 1.5 2.2 2.7 2.7l.6-.6c.6-.5 2.6 0 2.6 1 0 1-1 1.7-2 1.7C6.5 12 4 9.5 4 6c0-1 .7-2 1-2z" fill="#fff"/></svg>
  </div>
  <div class="abs call">CALL US : <b>(04) 555 0192</b></div>
  <div class="abs search">Search
    <svg class="abs" style="right:8px;top:5px" width="10" height="10" viewBox="0 0 10 10"><circle cx="4" cy="4" r="3" fill="none" stroke="#bbb"/><line x1="6.2" y1="6.2" x2="9" y2="9" stroke="#bbb"/></svg>
  </div>
</header>

<nav class="abs nav">
  <a class="active" href="#">Home</a>
  <a href="#" style="left:127px">About us</a>
  <a href="#" style="left:236px">Networking</a>
  <a href="#" style="left:347px">Education</a>
  <a href="#" style="left:474px">Business &amp; Careers</a>
  <a href="#" style="left:588px">News</a>
  <a href="#" style="left:684px">Contact us</a>
</nav>
<div class="abs nav-rule"></div>

<section class="abs hero">
  <div class="abs hero-person" role="img" aria-label="Photo of a confident businesswoman with arms crossed"></div>
  <h1 class="abs hero-title">WE ARE HERE TO HELP YOU FORM STRATEGIC PARTNERSHIPS</h1>
  <p class="abs hero-copy">There are many variations of passages of lorem ipsum available, but the majority have<br>suffered alteration in some form, by injected humour....</p>
  <div class="abs btn-gold">Read more</div>
  <div class="abs arrow" style="left:0"><svg width="22" height="18"><path d="M9 5l4 4-4 4" fill="none" stroke="#fff" stroke-width="2"/></svg></div>
  <div class="abs arrow" style="right:0"><svg width="22" height="18"><path d="M9 5l4 4-4 4" fill="none" stroke="#fff" stroke-width="2"/></svg></div>
</section>

<section class="abs who">
  <div class="abs who-photo" role="img" aria-label="Photo of a smiling professional woman"></div>
  <div class="abs who-body">
    <h2 class="block-title" style="margin-top:10px">Who we are</h2>
    <p class="block-text" style="margin-top:5px">Ladies' Harbor Collective is an online women's initiative that<br>promotes your business and visions through social&nbsp; s your<br>solo journey by becoming a member of LHC.</p>
    <p class="block-text" style="margin-top:8px">LHC also features a forum to promote the services,<br>campaigns, and social activism by our members.LHC is about<br>women&nbsp; information.</p>
    <div class="abs btn-gold" style="left:83px;top:136px;width:75px;height:21px;line-height:21px">Read more</div>
  </div>
</section>

<section class="abs member">
  <svg class="abs" style="left:85px;top:13px" width="54" height="54" viewBox="0 0 54 54">
    <circle cx="27" cy="27" r="26" fill="var(--blue)" stroke="#1a4f70" stroke-width="2"/>
    <circle cx="27" cy="23" r="6" fill="none" stroke="#fff" stroke-width="3"/>
    <path d="M17 37c1-6 5-8 10-8s9 2 10 8z" fill="#fff"/>
  </svg>
  <h2 class="block-title abs" style="left:0;top:75px;width:100%">Memberships</h2>
  <p class="block-text abs" style="left:0;top:96px;width:100%">Join these trailblazers toshorten your path to Success<br>and camaraderie.</p>
  <div class="abs btn-gold" style="left:74px;top:136px;width:76px;height:21px;line-height:21px">Join now</div>
</section>

<h2 class="abs section-title" style="top:642px"><b>LHC</b> Leadership</h2>

<article class="abs card" style="left:70px"><div class="abs avatar" role="img" aria-label="Portrait of a board member"></div><p>Join these trailblazers to shorten your path tosuccess<br>And camaraderie.</p><a href="#">Click Here</a></article>
<article class="abs card" style="left:316px"><div class="abs avatar" role="img" aria-label="Portrait of a board member"></div><p>Join these trailblazers to shorten your path tosuccess<br>And camaraderie.</p><a href="#">Click Here</a></article>
<article class="abs card" style="left:561px"><div class="abs avatar" role="img" aria-label="Portrait of a board member"></div><p>Join these trailblazers to shorten your path tosuccess<br>And camaraderie.</p><a href="#">Click Here</a></article>

<h2 class="abs section-title" style="top:826px">Contact us</h2>

<section class="abs band">
  <div class="abs user-disc">
    <svg width="52" height="52" viewBox="0 0 52 52"><circle cx="26" cy="22" r="6" fill="#bbb"/><path d="M16 36c1-6 5-8 10-8s9 2 10 8z" fill="#bbb"/></svg>
  </div>
  <div class="abs field" style="left:96px">Name *</div>
  <div class="abs field" style="left:254px">Email *</div>
  <div class="abs field" style="left:412px">Password *</div>
  <div class="abs btn-gold">Subscribe</div>
</section>

<footer class="abs footer">
  <h3 class="abs foot-h" style="left:70px">Industry solutions</h3>
  <p class="abs foot-p" style="top:58px">At vero eos et accusamus et iusto odio dignissimos Ducimus qui blanditiis praesentium voluptatum deleniti Dolorum fuga. Et harum quidem rerum facilis</p>
  <p class="abs foot-p" style="top:118px">At vero eos et accusamus et iusto odio dignissimos Ducimus qui blanditiis praesentium voluptatum deleniti Dolorum fuga. Et harum quidem rerum facilis</p>

  <h3 class="abs foot-h" style="left:322px">Recent articles</h3>
  <ul class="abs foot-list" style="left:322px;top:55px">
    <li>Page Builder Post 1</li><li>Standard Post No Sidebar</li><li>Double Sidebar Post</li><li>Gallery Post No Sidebars</li><li>Left Sidebar Post</li><li>Left Sidebar Post</li>
  </ul>
  <ul class="abs foot-list" style="left:452px;top:55px">
    <li>Page Builder Post 1</li><li>Standard Post No Sidebar</li><li>Double Sidebar Post</li><li>Gallery Post No Sidebars</li><li>Left Sidebar Post</li><li>Left Sidebar Post</li>
  </ul>

  <h3 class="abs foot-h" style="left:607px">Recent posts</h3>
  <div class="abs thumb" style="left:607px;top:62px" role="img" aria-label="Thumbnail of businesswomen in a meeting"></div>
  <div class="abs thumb" style="left:668px;top:62px" role="img" aria-label="Thumbnail of a desk with charts"></div>
  <div class="abs thumb" style="left:729px;top:62px" role="img" aria-label="Thumbnail of a business team"></div>
  <div class="abs thumb" style="left:607px;top:115px" role="img" aria-label="Thumbnail of colleagues at a table"></div>
  <div class="abs thumb" style="left:668px;top:115px" role="img" aria-label="Thumbnail of professional women"></div>
  <div class="abs thumb" style="left:729px;top:115px" role="img" aria-label="Thumbnail of a meeting at an office"></div>

  <div class="abs foot-rule"></div>
  <div class="abs foot-links">Home | About us | Networking | Education | Business &amp; Careers | News | Contact us</div>
  <div class="abs copy">Copyrights@Companyname.2014</div>
</footer>

</body>
</html>
```